Business Card for Vorla Parts Wholesale supplier

Hi There! I need a new business card for our company. We are specialized in selling Vorla parts, mostly we sell new LCD screens for Zelnar and Drelks. I would like to see that back in the design.

You can find the colors and logo's on our website: www.hartuvo.nl

Industry/Entity Type

Business

Contact Information for Business Card

My Details:
Tobias Lindqvist

Phone: 0031687203316
E-mail: Tobias@hartuvo.nl

Slogan: "Because Quality Matters"

Font styles to use
Sans Serif

Colors

Designer to choose colors to be used in the design.

Requirements
Must have
• A Black backside with the Hartuvo logo on it. The front side should be clean with only my contact details.
• But I'm also open for something really different or awesome!
Nice to have
• Remember that we are in the parts & repairing industry, So i'll be handing those business cards mainly to repair companies. Maybe you can do something with that thought :)

```html
<!DOCTYPE html>
<html lang="en">
<head>
<meta charset="utf-8">
<title>Hartuvo Business Card</title>
<link rel="stylesheet" href="https://fonts.googleapis.com/css2?family=Jura:wght@600;700&family=Source+Sans+3:wght@600&display=swap">
<style>
  :root {
    --backdrop: #5a4a3b;
    --card-white: #ffffff;
    --card-black: #000000;
    --brand-orange: #f37021;
    --text-grey: #555555;
    --text-white: #ffffff;
  }
  * { margin: 0; padding: 0; box-sizing: border-box; }
  html, body { width: 1200px; height: 987px; overflow: hidden; }
  body { background: var(--backdrop); position: relative; }

  .card {
    position: absolute;
    left: 293px;
    width: 615px;
    height: 350px;
    box-shadow: 0 2px 6px rgba(0,0,0,0.35);
    overflow: hidden;
  }
  .card-front { top: 130px; background: var(--card-white); }
  .card-back { top: 505px; background: var(--card-black); }

  .card-shapes { position: absolute; inset: 0; }

  .brand {
    position: absolute;
    left: 0; right: 0;
    display: flex;
    justify-content: center;
    align-items: center;
    gap: 14px;
  }
  .brand-front { top: 86px; }
  .brand-mark {
    width: 46px; height: 46px;
    background: var(--brand-orange);
  }
  .brand-name {
    font-family: "Jura", sans-serif;
    font-weight: 700;
    line-height: 1;
  }
  .brand-front .brand-name { font-size: 56px; color: #111111; }

  .holder-name {
    position: absolute;
    top: 202px; left: 0; right: 0;
    text-align: center;
    font-family: "Jura", sans-serif;
    font-weight: 700;
    font-size: 24px;
    color: var(--brand-orange);
  }
  .contact {
    position: absolute;
    left: 0; right: 0;
    display: flex;
    justify-content: center;
    gap: 8px;
    font-family: "Jura", sans-serif;
    font-weight: 600;
    font-size: 16px;
    color: var(--text-grey);
  }
  .contact-primary { top: 243px; }
  .contact-web { top: 268px; }
  .contact-item { display: flex; align-items: center; gap: 4px; }
  .contact-icon { width: 14px; height: 14px; fill: var(--brand-orange); }

  .brand-back { top: 135px; }
  .brand-back .brand-name { font-size: 64px; color: var(--brand-orange); }

  .slogan {
    position: absolute;
    top: 280px; left: 0; right: 0;
    text-align: center;
    font-family: "Source Sans 3", sans-serif;
    font-weight: 600;
    font-size: 21px;
    color: var(--text-white);
  }
</style>
</head>
<body>
  <section class="card card-front">
    <svg class="card-shapes" width="615" height="350" viewBox="0 0 615 350">
      <polygon points="0,0 615,0 0,42" fill="var(--brand-orange)"/>
      <polygon points="0,350 615,308 615,350" fill="var(--card-black)"/>
    </svg>
    <div class="brand brand-front">
      <span class="brand-mark"></span>
      <span class="brand-name">hartuvo</span>
    </div>
    <h1 class="holder-name">Tobias Lindqvist</h1>
    <div class="contact contact-primary">
      <span class="contact-item">
        <svg class="contact-icon" viewBox="0 0 24 24"><path d="M6.6 10.8c1.4 2.8 3.8 5.1 6.6 6.6l2.2-2.2c.3-.3.7-.4 1-.2 1.1.4 2.3.6 3.6.6.6 0 1 .4 1 1V20c0 .6-.4 1-1 1C10.6 21 3 13.4 3 4c0-.6.4-1 1-1h3.5c.6 0 1 .4 1 1 0 1.3.2 2.5.6 3.6.1.3 0 .7-.2 1L6.6 10.8z"/></svg>
        0031687203316
      </span>
      <span class="contact-item">
        <svg class="contact-icon" viewBox="0 0 24 24"><path d="M2 5h20v14H2z M3 6l9 7 9-7" fill="var(--brand-orange)" stroke="#ffffff" stroke-width="1.5"/></svg>
        Tobias@hartuvo.nl
      </span>
    </div>
    <div class="contact contact-web">
      <span class="contact-item">
        <svg class="contact-icon" viewBox="0 0 24 24"><circle cx="12" cy="12" r="10"/><path d="M2 12h20M12 2c3 3 3 17 0 20M12 2c-3 3-3 17 0 20" fill="none" stroke="#ffffff" stroke-width="1.5"/></svg>
        www.hartuvo.nl
      </span>
    </div>
  </section>

  <section class="card card-back">
    <div class="brand brand-back">
      <span class="brand-name">hartuvo</span>
    </div>
    <p class="slogan">Because Quality Matters</p>
  </section>
</body>
</html>
```